Global investment holding company - Business Card Design

Velto Range is a recently incorporated investment holding company. Based in Singapore, it has operations in global emerging markets in the transport & logistics, energy and livestock industries.

Its tagline "Growth Through Alliance" reflects the company's philosophy of helping countries progress through partnerships which generate employment and share benefits with its society.

We are looking for a business card that reflects our global presence - incorporating the logo design into the business card design. It must have a sophisticated, modern & corporate feel.

Target Market(s)

Investors and high level governmental officials

Industry/Entity Type

Investment

Requirements
Must have
• - Use of shades of blue in logo

-Profile picture

- Name: Dennis Orbeck
- Title: Chairman
- Email: dennis@veltorange-mail.com
- Mob: +65 9154 0826
- Tel: +65 6418 5092
- DID: + 65 6418 5093
- Address: 47 Harrow Lane, #08-03, Singapore 071286

- website: www.veltorange-mail.com

```html
<!DOCTYPE html>
<html lang="en">
<head>
<meta charset="UTF-8">
<title>Velto Range – Business Card</title>
<link rel="stylesheet" href="https://fonts.googleapis.com/css2?family=Arimo:wght@400;700&family=Open+Sans:wght@400;800&display=swap">
<style>
  :root {
    --stage: #e4e6ea;
    --navy: #1f3f8f;
    --blue-deep: #2c5aa8;
    --blue-mid: #4a82c6;
    --blue-pale: #9cc5ea;
    --paper: #ffffff;
    --grey-text: #7a7f88;
    --photo-tone-a: #8a94a6;
    --photo-tone-b: #3c4658;
  }
  * { margin: 0; padding: 0; box-sizing: border-box; }
  html, body { width: 1200px; height: 880px; overflow: hidden; }
  body {
    background: var(--stage);
    display: flex;
    align-items: center;
    justify-content: center;
    gap: 40px;
  }
  .card {
    position: relative;
    width: 540px;
    height: 310px;
    overflow: hidden;
    box-shadow: 0 10px 28px rgba(20, 30, 50, 0.22);
  }
  .card-art { position: absolute; inset: 0; width: 100%; height: 100%; display: block; }

  /* Back side */
  .card--back { background: var(--blue-deep); }
  .back-brand {
    position: absolute;
    right: 40px;
    top: 178px;
    color: var(--paper);
    font-family: "Open Sans", sans-serif;
    text-align: right;
  }
  .brand-row { display: flex; align-items: center; }
  .back-brand .brand-row { gap: 12px; justify-content: flex-end; }
  .back-brand .brand-mark {
    width: 40px; height: 40px; border-radius: 50%;
    background: var(--paper);
  }
  .back-brand .brand-name {
    font-weight: 800;
    font-size: 30px;
    line-height: 1;
    letter-spacing: 0.5px;
    text-transform: uppercase;
  }
  .back-brand .tagline {
    margin-top: 12px;
    font-size: 12px;
    letter-spacing: 1.6px;
    text-transform: uppercase;
  }
  .back-brand .site {
    margin-top: 6px;
    font-size: 12px;
    letter-spacing: 1px;
  }

  /* Front side */
  .card--front { background: var(--paper); }
  .portrait {
    position: absolute;
    left: 62px; top: 18px;
    width: 128px; height: 110px;
    border: 5px solid var(--paper);
    background: linear-gradient(160deg, var(--photo-tone-a), var(--photo-tone-b));
    box-shadow: 0 4px 10px rgba(0, 0, 0, 0.3);
  }
  .person {
    position: absolute;
    left: 205px; top: 104px;
    color: var(--paper);
    font-family: "Arimo", sans-serif;
  }
  .person .name {
    font-weight: 700; font-size: 17px; letter-spacing: 0.5px;
    text-transform: uppercase;
  }
  .person .role {
    font-weight: 700; font-size: 8px; letter-spacing: 0.8px;
    text-transform: uppercase;
  }
  .front-brand {
    position: absolute;
    right: 34px; top: 176px;
    font-family: "Open Sans", sans-serif;
    text-align: right;
  }
  .front-brand .brand-row { gap: 8px; justify-content: flex-end; }
  .front-brand .brand-mark {
    width: 24px; height: 24px; border-radius: 50%;
    background: var(--blue-mid);
  }
  .front-brand .brand-name {
    color: var(--navy);
    font-weight: 800;
    font-size: 19px;
    line-height: 1;
    text-transform: uppercase;
  }
  .front-brand .tagline {
    margin-top: 6px;
    color: var(--grey-text);
    font-size: 7.5px;
    letter-spacing: 1px;
    text-transform: uppercase;
  }
  .contact {
    position: absolute;
    left: 34px; top: 238px;
    width: 480px;
    font-family: "Arimo", sans-serif;
    color: var(--navy);
  }
  .contact .address { font-weight: 700; font-size: 12.5px; margin-bottom: 4px; }
  .contact .rows {
    display: grid;
    grid-template-columns: 250px 1fr;
    row-gap: 3px;
    font-size: 10.5px;
  }
  .contact .label { color: var(--grey-text); }
  .contact .web { font-weight: 700; font-size: 12px; }
</style>
</head>
<body>

  <section class="card card--back" aria-label="Business card, back">
    <svg class="card-art" viewBox="0 0 540 310" preserveAspectRatio="none" aria-hidden="true">
      <rect width="540" height="310" fill="var(--blue-deep)"/>
      <path d="M0,0 H540 V40 C380,60 200,120 0,200 Z" fill="var(--blue-mid)"/>
    </svg>
    <div class="back-brand">
      <div class="brand-row">
        <span class="brand-mark"></span>
        <span class="brand-name">Velto Range</span>
      </div>
      <p class="tagline">Growth Through Alliance</p>
      <p class="site">www.veltorange-mail.com</p>
    </div>
  </section>

  <section class="card card--front" aria-label="Business card, front">
    <svg class="card-art" viewBox="0 0 540 310" preserveAspectRatio="none" aria-hidden="true">
      <path d="M0,0 H540 V160 C360,165 170,145 0,118 Z" fill="var(--blue-deep)"/>
      <path d="M260,0 H540 V70 C440,66 340,40 260,0 Z" fill="var(--blue-pale)"/>
    </svg>

    <div class="portrait" role="img" aria-label="Profile photo of Dennis Orbeck, Chairman"></div>

    <div class="person">
      <p class="name">Dennis Orbeck</p>
      <p class="role">Chairman</p>
    </div>

    <div class="front-brand">
      <div class="brand-row">
        <span class="brand-mark"></span>
        <span class="brand-name">Velto Range</span>
      </div>
      <p class="tagline">Growth Through Alliance</p>
    </div>

    <div class="contact">
      <p class="address">47 Harrow Lane, #08-03, Singapore 071286</p>
      <div class="rows">
        <p><span class="label">mobile:</span> +65 9154 0826</p>
        <p><span class="label">tel:</span> +65 6418 5092</p>
        <p><span class="label">email:</span> dennis@veltorange-mail.com</p>
        <p><span class="label">did:</span> + 65 6418 5093</p>
        <p></p>
        <p><span class="label">web:</span> <span class="web">www.veltorange-mail.com</span></p>
      </div>
    </div>
  </section>

</body>
</html>
```